PowerPoint Re-Design and Template Needs a Designer's Eye!

I have the text, images and logo for a PowerPoint but need your Design and Template skills! Less than 20 pages, needs to be concise, include images, must have creative page layouts, include our floater-logo on every page, use sidebars or call-outs for important information, have color but not too much because this will be printed many times (our current colors are too dark). You can use bullet-points or paragraphs. You can also change the titles, font, color, layout - anything! This is YOUR PowerPoint to create the most impressive Template! We are an investment management firm located in New York City. Our investment returns are the very best in the industry and we want this PowerPoint to convey our "best in class" style.

Notes:
1) Please use the PPP outline attached.
2) I have attached a rough draft PPP. Please use the logos on page 2. Some pages do not have text, the final text will be available shortly.
3) I have attached examples you can reference.
4) Please include our floater-logo on every page.
5) Please feel free to ask questions or clarification.

Hi Designers, Thank you very much for your wonderful submissions! My partners and I are going through each submission in detail today and tomorrow. We'll be in touch over the next few days with additional questions and comments. Stay tuned! Best, Damon Quillfeather

High-net worth individuals and institutions. New York City, Wall Street.

Investment

• - Floater-logo on every page
- Sidebars or call-outs on several pages (you can decide which ones)
- Please include images; however, the PPP Template is the most important.

```html
<!DOCTYPE html>
<html lang="en">
<head>
<meta charset="utf-8">
<title>Executive Summary</title>
<link href="https://fonts.googleapis.com/css2?family=Roboto+Condensed:wght@400;700&family=Roboto:wght@400;500&family=Open+Sans:wght@400&display=swap" rel="stylesheet">
<style>
  :root {
    --orange: #f47900;
    --peach: #f7cba0;
    --row-grey: #eaeaea;
    --ink: #111111;
    --body-text: #4a4a4a;
    --cell-text: #4d4d4d;
    --rule: #b5b5b5;
    --footer: #676767;
    --white: #ffffff;
  }
  * { box-sizing: border-box; margin: 0; padding: 0; }
  html, body {
    width: 1200px; height: 900px; overflow: hidden;
    background: var(--white);
  }
  .slide {
    position: relative; width: 1200px; height: 900px;
    background: var(--white);
  }
  .slide-header {
    position: absolute; left: 0; top: 0; width: 1200px; height: 93px;
    background: var(--orange);
  }
  .slide-header::after {
    content: ""; position: absolute; left: 0; top: 96px; width: 1200px; height: 3px;
    background: var(--rule);
  }
  .slide-title {
    position: absolute; left: 27px; top: 22px;
    font: 700 40px/50px "Roboto Condensed", sans-serif;
    color: var(--ink); letter-spacing: 0.5px;
  }
  .brand {
    position: absolute; right: 22px; top: 22px; height: 50px;
    display: flex; align-items: center; gap: 10px;
    font: 700 26px/1 "Roboto Condensed", sans-serif;
    color: var(--white); letter-spacing: 1px;
  }
  .brand-dot {
    width: 40px; height: 40px; border-radius: 50%; background: var(--white);
  }
  .summary-intro {
    position: absolute; left: 76px; top: 170px; width: 1080px;
  }
  .summary-subtitle {
    font: 700 22px/32px "Open Sans", sans-serif; font-weight: 700;
    color: var(--orange);
  }
  .summary-text {
    margin-top: 2px;
    font: 400 19.5px/34.5px "Open Sans", sans-serif;
    color: var(--body-text);
  }
  .summary-table {
    position: absolute; left: 76px; top: 320px; width: 1085px;
    border-collapse: separate; border-spacing: 0 6px;
    table-layout: fixed; margin-top: -6px;
  }
  .summary-table th {
    height: 61px; background: var(--orange); color: var(--white);
    font: 500 27px/1 "Roboto", sans-serif; text-align: center;
  }
  .summary-table td {
    height: 55px; text-align: center;
    font: 400 22px/1 "Roboto", sans-serif; color: var(--cell-text);
  }
  .summary-table tbody tr:nth-child(odd) td { background: var(--row-grey); }
  .summary-table tbody tr:nth-child(even) td { background: var(--peach); }
  .slide-footer {
    position: absolute; left: 0; top: 860px; width: 1200px; height: 40px;
    background: var(--footer); color: var(--white);
    display: flex; justify-content: space-between; align-items: center;
    padding: 0 9px 0 8px;
    font: 400 18px/1 "Roboto Condensed", sans-serif;
  }
</style>
</head>
<body>
<main class="slide">
  <header class="slide-header">
    <h1 class="slide-title">EXECUTIVE SUMMARY</h1>
    <div class="brand"><span class="brand-dot"></span>HALCREST</div>
  </header>

  <section class="summary-intro">
    <h2 class="summary-subtitle">Table Subtitle Here</h2>
    <p class="summary-text">Lorem ipsum dolor sit Lorem ipsum dolor sit&nbsp; Lorem ipsum dolor sit Lorem ipsum dolor sit&nbsp; Lorem ipsum dolor sit Lorem ipsum dolor sit&nbsp; Lorem ipsum dolor sit Lorem ipsum dolor sit&nbsp; Lorem ipsum dolor sit Lorem ipsum dolor sit&nbsp; Lorem ipsum dolor sit Lorem ipsum dolor sit</p>
  </section>

  <table class="summary-table">
    <thead>
      <tr><th>TABLE TITLE HERE</th><th>TABLE TITLE HERE</th><th>TABLE TITLE HERE</th></tr>
    </thead>
    <tbody>
      <tr><td>Subtext here</td><td>Subtext here</td><td>Subtext here</td></tr>
      <tr><td>Subtext here</td><td>Subtext here</td><td>Subtext here</td></tr>
      <tr><td>Subtext here</td><td>Subtext here</td><td>Subtext here</td></tr>
      <tr><td>Subtext here</td><td>Subtext here</td><td>Subtext here</td></tr>
      <tr><td>Subtext here</td><td>Subtext here</td><td>Subtext here</td></tr>
      <tr><td>Subtext here</td><td>Subtext here</td><td>Subtext here</td></tr>
    </tbody>
  </table>

  <footer class="slide-footer">
    <span class="footer-author">Damon Quillfeather 2015</span>
    <span class="footer-page">Page : 01</span>
  </footer>
</main>
</body>
</html>
```